Emerging Ed-Tech Startup seeking Stationery Designs!

We are in need of basic set of stationery designs to be used for our business operations, letters, emails, and in-office materials. We are a technology startup enhancing on campus work experience offerings by establishing a collaborative work environment for the completion of such tasks.

Our colors are Vibrant Tiffany Blue/Black/White.

Website: www.campusnorthway.com (Still under construction aside from the landing pages)

Please make sure the designs use a brighter more vibrant tiffany blue color than seen in the image files uploaded. We are not using those materials.

Our logo has been added as a file as well, please use that for any designs (include that logo). Thank you.

```html
<!DOCTYPE html>
<html lang="en">
<head>
<meta charset="utf-8">
<title>Campus Northway — Stationery Set</title>
<link href="https://fonts.googleapis.com/css2?family=Open+Sans:wght@400;600;700&display=swap" rel="stylesheet">
<style>
  :root{
    --tiffany:#5cf2cd;
    --ink:#1b1b1b;
    --paper:#ffffff;
    --stage:#e4e6e7;
    --ghost:#eff1f1;
    --muted:#3a3a3a;
    --rule:#6a6a6a;
  }
  *{box-sizing:border-box;margin:0;padding:0}
  html,body{width:1200px;height:540px;overflow:hidden}
  body{background:var(--stage);font-family:"Open Sans",Arial,sans-serif;color:var(--ink);position:relative}
  .sheet{position:absolute;background:var(--paper);overflow:hidden;box-shadow:0 2px 6px rgba(0,0,0,.18)}

  /* brand lockup */
  .brand{position:absolute;display:flex;align-items:center;gap:4px;font-weight:700;line-height:1.02;text-transform:uppercase;color:var(--ink)}
  .brand-mark{background:var(--tiffany);flex:none}
  .brand-name{display:block}
  .brand--sm{font-size:11px}
  .brand--sm .brand-mark{width:11px;height:11px}
  .brand--xs{font-size:7px;gap:3px}
  .brand--xs .brand-mark{width:7px;height:7px}
  .brand--light{color:var(--paper)}
  .ghost-name{position:absolute;font-weight:700;text-transform:uppercase;color:var(--ghost);line-height:1;text-align:center}

  /* edge bands */
  .band{position:absolute;left:0;right:0}
  .band--top{top:0;height:5px}
  .band--bottom{bottom:0;height:6px}

  /* contact list */
  .contacts{list-style:none;position:absolute;font-size:5.4px;line-height:1.55;color:var(--muted)}
  .contacts li{display:flex;align-items:center;gap:3px}
  .icon{width:5px;height:5px;fill:var(--ink);flex:none}

  /* letterhead */
  .letterhead{left:30px;top:28px;width:340px;height:440px}
  .letterhead .band--top{background:linear-gradient(100deg,var(--tiffany) 0 62%,var(--ink) 62% 100%)}
  .letterhead .band--bottom{background:linear-gradient(100deg,var(--ink) 0 36%,var(--tiffany) 36% 100%)}
  .letterhead .contacts{right:6px;top:17px;border-left:.6px solid var(--ink);padding-left:4px}
  .letterhead .ghost-name{left:40px;top:170px;width:260px;font-size:42px}
  .address-line{position:absolute;font-size:6.4px;letter-spacing:.2px;color:var(--muted)}
  .letterhead .address-line{bottom:14px;left:0;right:0;text-align:center}

  /* fax */
  .fax{left:406px;top:28px;width:340px;height:440px;background:linear-gradient(160deg,#ffffff 0%,#f4f4f4 55%,#e9e9e9 100%)}
  .fax .band--top{background:linear-gradient(100deg,var(--tiffany) 0 62%,var(--ink) 62% 100%)}
  .fax .band--bottom{background:linear-gradient(100deg,var(--ink) 0 9%,var(--tiffany) 9% 100%)}
  .fax .address-block{position:absolute;right:10px;top:27px;font-size:6.4px;line-height:1.25;border-left:.6px solid var(--ink);padding-left:4px;color:var(--muted)}
  .fax-title{position:absolute;left:18px;top:93px;font-size:18px;font-weight:400;letter-spacing:.5px}
  .fax-fields{position:absolute;left:18px;top:130px;width:291px;display:grid;grid-template-columns:173px 118px;row-gap:6px}
  .fax-field{font-size:5.2px;border-bottom:.8px solid var(--rule);padding-bottom:1.5px;height:12px;display:flex;align-items:flex-end}
  .fax-options{position:absolute;left:18px;top:216px;display:flex;gap:13px;font-size:5.4px}
  .fax-options li{list-style:none;display:flex;align-items:center;gap:3px}
  .checkbox{width:6px;height:6px;border:.7px solid var(--ink);background:var(--paper)}
  .fax .contacts{left:0;right:0;bottom:13px;display:flex;justify-content:center;gap:10px}

  /* envelopes */
  .envelope{position:absolute;overflow:hidden}
  .envelope--back{left:802px;top:30px;width:380px;height:170px;background:#f3f4f4}
  .envelope--middle{left:790px;top:104px;width:380px;height:100px;background:#f7f7f7;box-shadow:0 2px 5px rgba(0,0,0,.15)}
  .flap{position:absolute;left:0;top:0;width:100%}
  .envelope--back .brand{left:158px;top:24px}
  .envelope--middle .brand{left:156px;top:18px}
  .envelope--front{left:764px;top:189px;width:380px;height:171px;background:var(--paper);box-shadow:0 2px 6px rgba(0,0,0,.2)}
  .envelope--front .band--top{height:6px;background:linear-gradient(100deg,var(--tiffany) 0 62%,var(--ink) 62% 100%)}
  .envelope--front .band--bottom{height:6px;background:linear-gradient(100deg,var(--ink) 0 38%,var(--tiffany) 38% 100%)}
  .envelope--front .brand{left:10px;top:18px}
  .envelope--front .ghost-name{right:14px;top:30px;width:150px;font-size:24px}
  .envelope--front .return-address{position:absolute;left:7px;top:178px;font-size:6.2px;line-height:1.45;top:141px}
  .return-address strong{font-weight:600}

  /* business cards */
  .card{left:786px;top:389px;width:140px;height:80px}
  .card--back{left:938px}
  .card .band--top{height:2.5px;background:linear-gradient(100deg,var(--tiffany) 0 62%,var(--ink) 62% 100%)}
  .card .band--bottom{height:3.5px;background:linear-gradient(100deg,var(--ink) 0 40%,var(--tiffany) 40% 100%)}
  .card--front .brand{left:48px;top:9px}
  .card-holder{position:absolute;left:6px;top:46px;width:56px;text-align:right;font-size:4.6px;line-height:1.35}
  .card-holder .name{font-size:5px;font-weight:600}
  .card--front .contacts{left:66px;top:45px;font-size:4.2px;border-left:.5px solid var(--ink);padding-left:3px;line-height:1.5}
  .card--front .icon{width:4px;height:4px}
  .card--back .brand-mark{position:absolute;left:57px;top:11px;width:26px;height:26px;background:var(--tiffany)}
  .card--back .brand{left:0;right:0;top:41px;justify-content:center}
  .card-tagline{position:absolute;left:0;right:0;top:56px;text-align:center;font-size:5.2px;line-height:1.4}

  /* option labels */
  .option-label{position:absolute;top:480px;font-size:22px;font-weight:400;color:var(--muted)}
  .option-label--one{left:129px}
  .option-label--two{left:512px}
</style>
</head>
<body>

<svg width="0" height="0" style="position:absolute" aria-hidden="true">
  <symbol id="i-phone" viewBox="0 0 10 10"><path d="M2.2 .6l1.6 2-1 1a6 6 0 0 0 3.6 3.6l1-1 2 1.6-1.2 1.6C4.6 9.2.8 5.4.6 1.8z"/></symbol>
  <symbol id="i-mail" viewBox="0 0 10 10"><path d="M0 2h10v6H0zM.8 2.6L5 5.6l4.2-3"/></symbol>
  <symbol id="i-web" viewBox="0 0 10 10"><circle cx="5" cy="5" r="4.6"/></symbol>
</svg>

<!-- Letterhead -->
<section class="sheet letterhead" aria-label="Letterhead">
  <div class="band band--top"></div>
  <div class="brand brand--sm" style="left:11px;top:16px"><span class="brand-mark"></span><span><span class="brand-name">Campus</span><span class="brand-name">Northway</span></span></div>
  <ul class="contacts">
    <li><svg class="icon"><use href="#i-phone"/></svg>+91 20 4815372</li>
    <li><svg class="icon"><use href="#i-phone"/></svg>+91 14 5520937</li>
    <li><svg class="icon"><use href="#i-mail"/></svg>hello@campusnorthway.com</li>
    <li><svg class="icon"><use href="#i-web"/></svg>www.campusnorthway.com</li>
  </ul>
  <div class="ghost-name" aria-hidden="true">Campus<br>Northway</div>
  <p class="address-line">Street Name, City Name State Zipcode</p>
  <div class="band band--bottom"></div>
</section>

<!-- Fax sheet -->
<section class="sheet fax" aria-label="Fax cover sheet">
  <div class="band band--top"></div>
  <div class="brand brand--sm" style="left:14px;top:18px"><span class="brand-mark"></span><span><span class="brand-name">Campus</span><span class="brand-name">Northway</span></span></div>
  <p class="address-block">Street Name, City Name<br>State Zipcode</p>
  <h1 class="fax-title">FAX</h1>
  <div class="fax-fields">
    <span class="fax-field">To :</span><span class="fax-field">From :</span>
    <span class="fax-field">Fax :</span><span class="fax-field">Pages :</span>
    <span class="fax-field">Phone :</span><span class="fax-field">Date :</span>
    <span class="fax-field">Re :</span><span class="fax-field">CC :</span>
  </div>
  <ul class="fax-options">
    <li><span class="checkbox"></span>Urgent</li>
    <li><span class="checkbox"></span>For Review</li>
    <li><span class="checkbox"></span>Please Comment</li>
    <li><span class="checkbox"></span>Please Reply</li>
    <li><span class="checkbox"></span>Please Recycle</li>
  </ul>
  <ul class="contacts">
    <li><svg class="icon"><use href="#i-phone"/></svg>+91 20 4815372</li>
    <li><svg class="icon"><use href="#i-phone"/></svg>+91 14 5520937</li>
    <li><svg class="icon"><use href="#i-mail"/></svg>hello@campusnorthway.com</li>
    <li><svg class="icon"><use href="#i-web"/></svg>www.campusnorthway.com</li>
  </ul>
  <div class="band band--bottom"></div>
</section>

<!-- Envelopes -->
<section class="envelope envelope--back" aria-label="Envelope back, dark flap">
  <svg class="flap" viewBox="0 0 380 80" height="80" preserveAspectRatio="none"><path d="M0 0H380V14Q372 24 330 40L214 76Q190 82 166 76L50 40Q8 24 0 14Z" fill="var(--ink)"/></svg>
  <div class="brand brand--xs" style="color:var(--tiffany)"><span class="brand-mark"></span><span><span class="brand-name">Campus</span><span class="brand-name">Northway</span></span></div>
</section>

<section class="envelope envelope--middle" aria-label="Envelope back, tiffany flap">
  <svg class="flap" viewBox="0 0 380 70" height="70" preserveAspectRatio="none"><path d="M0 0H380V8Q374 18 340 30L212 64Q190 70 168 64L40 30Q6 18 0 8Z" fill="var(--tiffany)"/></svg>
  <div class="brand brand--xs brand--light"><span class="brand-mark" style="background:var(--paper)"></span><span><span class="brand-name">Campus</span><span class="brand-name">Northway</span></span></div>
</section>

<section class="envelope envelope--front" aria-label="Envelope front">
  <div class="band band--top"></div>
  <div class="brand brand--sm"><span class="brand-mark"></span><span><span class="brand-name">Campus</span><span class="brand-name">Northway</span></span></div>
  <div class="ghost-name" aria-hidden="true">Campus<br>Northway</div>
  <p class="return-address">Street Name, City Name, State Zipcode<br><strong>www.campusnorthway.com</strong></p>
  <div class="band band--bottom"></div>
</section>

<!-- Business cards -->
<section class="sheet card card--front" aria-label="Business card front">
  <div class="band band--top"></div>
  <div class="brand brand--xs"><span class="brand-mark"></span><span><span class="brand-name">Campus</span><span class="brand-name">Northway</span></span></div>
  <div class="card-holder">
    <div class="name">Your Name</div>
    <div>Title</div>
    <div style="margin-top:3px">Street Name, City Name<br>State Zip Code</div>
  </div>
  <ul class="contacts">
    <li><svg class="icon"><use href="#i-phone"/></svg>+91 20 4815372</li>
    <li><svg class="icon"><use href="#i-phone"/></svg>+91 14 5520937</li>
    <li><svg class="icon"><use href="#i-mail"/></svg>hello@campusnorthway.com</li>
    <li><svg class="icon"><use href="#i-web"/></svg>www.campusnorthway.com</li>
  </ul>
  <div class="band band--bottom"></div>
</section>

<section class="sheet card card--back" aria-label="Business card back">
  <div class="band band--top"></div>
  <span class="brand-mark"></span>
  <div class="brand brand--xs"><span class="brand-name">Campus Northway</span></div>
  <p class="card-tagline">Experience • Education • Excellence<br>www.campusnorthway.com</p>
  <div class="band band--bottom"></div>
</section>

<p class="option-label option-label--one">Option-1</p>
<p class="option-label option-label--two">Option-2</p>

</body>
</html>
```